Mobile Fitness snd Therapy Business Card Design

I need a business card designed for my mobile fitness and therapy business.

Please view the images that I have uploaded. I like the simplicity of the design that I have attached. I adapted it with my information

Target Market(s)

Those seeking personal training, injury rehabilitation or massage therapy.

Industry/Entity Type

Business

Contact Information for Business Card

Derek Fulham - MSc, CAT(C), RMT, CSCS, Pn2
e-mail: derek@vantrelo.com
website: www.vantrelo.com
instagram: @derek_fulham

Font styles to use
Sans Serif

Colors
3176b5
0355a3

Requirements
Must have
• "Contact us to receive a FREE assessment"
• Services offered:
• Personal Training
• Golf Fitness
• Injury Rehab
• Massage Therapy
• Yoga
Nice to have
• Consistent colours with brand
• - Dark Blue: #232837
• - Blue: #5096f0
• Consistent look/feel with the website: www.vantrelo.com

```html
<!DOCTYPE html>
<html lang="en">
<head>
<meta charset="utf-8">
<title>Vantrelo Business Card</title>
<link rel="stylesheet" href="https://fonts.googleapis.com/css2?family=Open+Sans:ital,wght@0,400;0,600;0,700;0,800;1,400&display=swap">
<style>
  :root {
    --navy: #232837;
    --blue-deep: #3460b0;
    --white: #ffffff;
    --backdrop: #e9eaed;
  }
  * { box-sizing: border-box; margin: 0; padding: 0; }
  html, body {
    width: 1200px; height: 1200px; overflow: hidden;
    background: var(--backdrop);
    font-family: "Open Sans", Arial, sans-serif;
  }
  .card {
    position: absolute; left: 150px;
    width: 900px; height: 514px;
    overflow: hidden;
    box-shadow: 0 6px 20px rgba(0,0,0,0.12);
  }
  .card--back { top: 56px; background: var(--navy); color: var(--white); }
  .card--front { top: 630px; background: var(--white); color: var(--navy); }

  .offer {
    position: absolute; left: 64px; top: 58px;
    font-size: 19px; letter-spacing: 2px; font-weight: 600;
  }
  .brand { font-weight: 800; letter-spacing: 10px; line-height: 1; }
  .tagline { font-weight: 700; letter-spacing: 6px; white-space: nowrap; }
  .card--back .identity {
    position: absolute; left: 0; right: 0; top: 150px; text-align: center;
  }
  .card--back .brand { font-size: 104px; }
  .card--back .tagline { font-size: 26px; margin-top: 14px; }
  .services {
    position: absolute; left: 64px; bottom: 56px;
    font-size: 19px; line-height: 1.45;
  }
  .services__title { font-weight: 700; letter-spacing: 1px; }
  .services__list { list-style: none; display: flex; gap: 10px; font-weight: 600; }
  .services__list li + li::before { content: "•"; margin-right: 10px; }

  .card--front .identity { position: absolute; left: 64px; top: 80px; }
  .card--front .brand { font-size: 104px; }
  .card--front .tagline { font-size: 26px; margin-top: 14px; }
  .contact-row {
    position: absolute; left: 64px; top: 290px;
    display: flex; align-items: stretch; gap: 28px;
  }
  .person__name { font-size: 40px; font-weight: 400; letter-spacing: -0.5px; line-height: 1.1; }
  .person__credentials { font-size: 15px; font-weight: 600; margin-top: 4px; }
  .divider { width: 2px; background: var(--blue-deep); }
  .contacts { list-style: none; font-size: 18px; line-height: 1.7; }
  .contacts li { display: flex; align-items: center; gap: 10px; }
  .contacts svg { width: 18px; height: 18px; flex: none; }
</style>
</head>
<body>

<section class="card card--back">
  <p class="offer">“Contact us to receive a FREE assessment”</p>
  <div class="identity">
    <div class="brand">VANTRELO</div>
    <div class="tagline">NUTRITION - FITNESS - HEALTH</div>
  </div>
  <div class="services">
    <p class="services__title">Services offered:</p>
    <ul class="services__list">
      <li>Personal Training</li>
      <li>Golf Fitness</li>
      <li>Injury Rehab</li>
      <li>Massage Therapy</li>
      <li>Yoga</li>
    </ul>
  </div>
</section>

<section class="card card--front">
  <div class="identity">
    <div class="brand">VANTRELO</div>
    <div class="tagline">NUTRITION - FITNESS - HEALTH</div>
  </div>
  <div class="contact-row">
    <div class="person">
      <p class="person__name">Derek Fulham</p>
      <p class="person__credentials">MSc, CAT(C), RMT, CSCS, Pn2</p>
    </div>
    <div class="divider"></div>
    <ul class="contacts">
      <li>
        <svg viewBox="0 0 18 18" aria-hidden="true"><rect x="1" y="3" width="16" height="12" rx="1" fill="var(--blue-deep)"/><path d="M1.5 4 9 10 16.5 4" stroke="#fff" stroke-width="1.5" fill="none"/></svg>
        derek@vantrelo.com
      </li>
      <li>
        <svg viewBox="0 0 18 18" aria-hidden="true"><circle cx="9" cy="9" r="8" fill="var(--blue-deep)"/></svg>
        www.vantrelo.com
      </li>
      <li>
        <svg viewBox="0 0 18 18" aria-hidden="true"><rect x="1" y="1" width="16" height="16" rx="3" fill="var(--blue-deep)"/></svg>
        @derek_fulham
      </li>
    </ul>
  </div>
</section>

</body>
</html>
```